Clear Plastic Card Design

I am looking to have a business card designed from my logo icon. I am looking to match the style of a different business card I have attached in the files.
Looking for a card that is plastic, with layers of transparency in the shape of my logo icon (also attached in the files) - not a circle like the other card. The winning design will incorporate the red icon logo on the front and back and include the charity's name, "Light for the Weary Souls" in the same or similar font, as well as an email and phone number. For now, use the email: email@lightfortheweary-mail.org and the phone number 555-382-7194.
We like how the sample business card has transparency, partial and full opacity layers and a matching color scheme. Files will need to be in vector so that our business card printing company can work with it.
UPDATE:
We've some excellent designs in, thank you everyone! I got an early review from the owner, and he requested a minor redirect to find his perfect design. He wants the design to stand out by NOT being a rectangle. Try instead a circle, square, or best yet - something that falls in the outline of the logo icon, either fully or partially. Thank you, everyone!
Light for the Weary Souls text should be incorporated as well as a phone and email.

```html
<!DOCTYPE html>
<html lang="en">
<head>
<meta charset="utf-8">
<title>Light for the Weary Souls – Business Card</title>
<link rel="stylesheet" href="https://fonts.googleapis.com/css2?family=Poppins:wght@400;500;600&display=swap">
<style>
  :root {
    --backdrop: #e6ded1;
    --clear-plastic: rgba(255, 255, 255, 0.42);
    --plastic-edge: rgba(255, 255, 255, 0.75);
    --brand-red: #c0101f;
    --brand-red-deep: #a90c1a;
    --ink: #2b2523;
    --white: #fbf6f1;
  }
  * { margin: 0; padding: 0; box-sizing: border-box; }
  html, body { width: 1200px; height: 539px; overflow: hidden; }
  body {
    background: var(--backdrop);
    font-family: "Poppins", sans-serif;
    position: relative;
  }
  .card {
    position: absolute;
    top: 150px;
    width: 486px;
    height: 264px;
    border-radius: 18px;
    overflow: hidden;
  }
  .card--front {
    left: 79px;
    background: var(--clear-plastic);
    border: 1px solid var(--plastic-edge);
  }
  .card--back {
    left: 661px;
    background: linear-gradient(135deg, #c9202f 0%, var(--brand-red) 55%, var(--brand-red-deep) 100%);
  }

  /* front: brand block */
  .brand {
    position: absolute;
    left: 18px;
    top: 48px;
    display: flex;
    align-items: center;
    gap: 10px;
  }
  .brand__square {
    width: 22px; height: 22px;
    background: var(--brand-red);
  }
  .brand__name {
    font-size: 16px;
    font-weight: 400;
    line-height: 1.1;
    color: var(--ink);
  }

  /* front: person */
  .person {
    position: absolute;
    right: 20px;
    top: 18px;
    text-align: right;
  }
  .person__name {
    font-size: 22px;
    line-height: 1.1;
    color: var(--brand-red);
  }
  .person__first { font-weight: 600; }
  .person__last { font-weight: 400; color: #d4361f; }
  .person__role {
    font-size: 11px;
    font-weight: 500;
    color: #1b1b1b;
    margin-top: 4px;
  }
  .accent-bar {
    position: absolute;
    right: 1px;
    top: 21px;
    width: 11px;
    height: 35px;
    background: var(--brand-red);
  }

  /* front: contact band */
  .contact-band {
    position: absolute;
    left: 0; right: 0; bottom: 0;
    height: 132px;
    background: linear-gradient(100deg, #c81a2a 0%, var(--brand-red) 60%, var(--brand-red-deep) 100%);
    color: var(--white);
  }
  .address {
    position: absolute;
    left: 15px;
    top: 14px;
    font-size: 12px;
    line-height: 16px;
    letter-spacing: 0.3px;
  }
  .contact-list {
    position: absolute;
    left: 15px;
    top: 70px;
    list-style: none;
    font-size: 12px;
    letter-spacing: 0.3px;
  }
  .contact-list li {
    display: flex;
    align-items: center;
    gap: 8px;
    height: 16px;
  }
  .contact-list svg { width: 11px; height: 11px; flex: none; }
  .band-mark {
    position: absolute;
    right: 18px;
    top: 40px;
    text-align: right;
    font-size: 15px;
    font-weight: 500;
    line-height: 1.15;
    color: rgba(255, 236, 230, 0.85);
  }

  /* back */
  .back-mark {
    position: absolute;
    left: 92px;
    top: 138px;
    display: flex;
    align-items: center;
    gap: 14px;
  }
  .back-mark__square {
    width: 34px; height: 34px;
    background: var(--white);
  }
  .back-mark__name {
    font-size: 28px;
    font-weight: 400;
    line-height: 1.05;
    color: var(--white);
  }
</style>
</head>
<body>
  <section class="card card--front" aria-label="Card front">
    <div class="brand">
      <span class="brand__square"></span>
      <span class="brand__name">Light for the<br>Weary Souls</span>
    </div>

    <div class="person">
      <p class="person__name"><span class="person__first">Marta</span> <span class="person__last">Velinska</span></p>
      <p class="person__role">Founder &amp; CEO</p>
    </div>
    <span class="accent-bar"></span>

    <div class="contact-band">
      <p class="address">780 Ashgrove Ln. Suite 310<br>Dayton, OH 45402</p>
      <ul class="contact-list">
        <li>
          <svg viewBox="0 0 12 12" aria-hidden="true"><path d="M2.5 1h2l1 2.5-1.3 1a6 6 0 0 0 3.3 3.3l1-1.3L11 7.5v2A1.5 1.5 0 0 1 9.5 11 8.5 8.5 0 0 1 1 2.5 1.5 1.5 0 0 1 2.5 1z" fill="currentColor"/></svg>
          555-382-7194
        </li>
        <li>
          <svg viewBox="0 0 12 12" aria-hidden="true"><circle cx="6" cy="6" r="5" fill="none" stroke="currentColor" stroke-width="1.2"/><path d="M1 6h10M6 1c2 2 2 8 0 10M6 1c-2 2-2 8 0 10" fill="none" stroke="currentColor" stroke-width="1"/></svg>
          www.lightfortheweary.org
        </li>
        <li>
          <svg viewBox="0 0 12 12" aria-hidden="true"><rect x="1" y="2.5" width="10" height="7" fill="none" stroke="currentColor" stroke-width="1.2"/><path d="M1 2.5 6 7l5-4.5" fill="none" stroke="currentColor" stroke-width="1.2"/></svg>
          email@lightfortheweary-mail.org
        </li>
      </ul>
      <p class="band-mark">Light for the<br>Weary Souls</p>
    </div>
  </section>

  <section class="card card--back" aria-label="Card back">
    <div class="back-mark">
      <span class="back-mark__square"></span>
      <span class="back-mark__name">Light for the<br>Weary Souls</span>
    </div>
  </section>
</body>
</html>
```